Need CATCHY/VIVID Banner design for my new UTV/ATV/Off Road Vehicle turn signal/lighting company

I need a banner ad designed so I can advertise on several different ATV (all terrain vehicle), UTV (Utility Vehicles), Golf Cart and Off-Road Vehicle forums. Ads need to be very catchy and produce a call to action. Action is getting hits to my website. Our main business is selling turn signal kits to make your side by side or your ATV/UTV street legal, as some states now allow you to drive these on public roads if you have the following items: Turn Signals, Horn, Lighted license plate bracket, headlights and brake lights. We sell all of these items for just about any model vehicle out there. Our call to action for this banner would be to get more website visits.

Target Market(s)

Off-road/outdoor enthusiasts,

Industry/Entity Type

Car Accessorie

Font styles to use
Sans Serif

Requirements
Must have
• Ad size need to be either 728x90 or 300x250. Colorful ad with an off-road vehicle integrated to the design (think UTV, side-by-side, etc.
Nice to have
• Nice to haves would be anything that makes this banner ad stand out on very boring web pages.
Should not have
• anything dull

```html
<!DOCTYPE html>
<html lang="en">
<head>
<meta charset="utf-8">
<title>Ridelite – ATV &amp; UTV Signal Lighting</title>
<link href="https://fonts.googleapis.com/css2?family=Montserrat:wght@700;800;900&display=swap" rel="stylesheet">
<style>
  :root {
    --ink: #050505;
    --white: #ffffff;
    --yellow: #ffc21a;
    --orange: #f7a400;
    --red: #d8121b;
    --maroon: #7a0f12;
    --deep: #3a0708;
  }
  html, body {
    margin: 0;
    padding: 0;
    width: 1200px;
    height: 1000px;
    overflow: hidden;
    background: var(--ink);
  }
  .banner {
    position: relative;
    width: 1200px;
    height: 1000px;
    background: var(--ink);
    font-family: "Montserrat", Arial, sans-serif;
    overflow: hidden;
  }
  .banner__shapes {
    position: absolute;
    inset: 0;
  }
  .brand {
    position: absolute;
    left: 0;
    top: 60px;
    width: 600px;
    text-align: center;
    color: var(--white);
  }
  .brand__name {
    display: inline-flex;
    align-items: center;
    gap: 18px;
    font-size: 84px;
    font-weight: 900;
    color: var(--yellow);
    letter-spacing: 1px;
    line-height: 1;
  }
  .brand__dot {
    width: 40px;
    height: 40px;
    border-radius: 50%;
    background: var(--red);
  }
  .brand__tagline {
    margin: 46px 0 0;
    font-size: 44px;
    font-weight: 800;
    line-height: 1;
    letter-spacing: 0.5px;
  }
  .brand__sub {
    margin: 14px 0 0;
    font-size: 31px;
    font-weight: 800;
    line-height: 1;
    letter-spacing: 0.5px;
  }
  .headline {
    position: absolute;
    left: 56px;
    top: 468px;
    margin: 0;
    color: var(--yellow);
    font-size: 86px;
    font-weight: 900;
    line-height: 92px;
    letter-spacing: 1px;
  }
  .headline__line { display: block; }
  .subhead {
    position: absolute;
    left: 56px;
    top: 652px;
    margin: 0;
    color: var(--white);
    font-size: 54px;
    font-weight: 800;
    line-height: 1;
  }
  .detail {
    position: absolute;
    left: 56px;
    top: 736px;
    margin: 0;
    color: var(--white);
    font-size: 34px;
    font-weight: 800;
    line-height: 46px;
  }
  .features {
    position: absolute;
    left: 56px;
    top: 858px;
    display: flex;
    gap: 40px;
    align-items: center;
  }
  .features svg { display: block; }
</style>
</head>
<body>
<main class="banner">
  <svg class="banner__shapes" width="1200" height="1000" viewBox="0 0 1200 1000">
    <defs>
      <linearGradient id="terrain" x1="0" y1="0" x2="0.3" y2="1">
        <stop offset="0" stop-color="#8fa3b4"/>
        <stop offset="0.18" stop-color="#a79a86"/>
        <stop offset="0.4" stop-color="#3b2d26"/>
        <stop offset="0.65" stop-color="#5c3c2a"/>
        <stop offset="1" stop-color="#a77b55"/>
      </linearGradient>
    </defs>
    <polygon class="stripe stripe--deep" points="600,0 1200,0 1200,1000 720,1000 470,490" fill="var(--deep)"/>
    <polygon class="stripe stripe--maroon" points="636,0 1200,0 1200,1000 750,1000 500,490" fill="var(--maroon)"/>
    <polygon class="stripe stripe--red" points="690,0 1200,0 1200,1000 800,1000 550,490" fill="var(--red)"/>
    <polygon class="stripe stripe--yellow" points="740,0 1200,0 1200,1000 860,1000 600,490" fill="var(--orange)"/>
    <polygon class="stripe stripe--gold" points="760,0 1200,0 1200,1000 885,1000 625,490" fill="var(--yellow)"/>
    <polygon class="hero-photo" role="img" aria-label="Photo of a black sport UTV with red roll cage and bumper on rocky desert terrain"
             points="790,0 1200,0 1200,1000 920,1000 650,490" fill="url(#terrain)"/>
  </svg>

  <header class="brand">
    <div class="brand__name"><span class="brand__dot"></span>RIDELITE</div>
    <p class="brand__tagline">TURN SIGNAL KITS</p>
    <p class="brand__sub">&amp; LIGHTING ACCESSORIES</p>
  </header>

  <h1 class="headline">
    <span class="headline__line">ATV &amp; UTV</span>
    <span class="headline__line">VECHICLE</span>
  </h1>
  <p class="subhead">SIGNAL LIGHTING</p>
  <p class="detail">OFF ROAD VEHICLE<br>TURN SIGNAL</p>

  <div class="features" aria-label="Brake lights, headlights, horn, turn signals">
    <svg width="76" height="64" viewBox="0 0 76 64" fill="none" stroke="var(--yellow)" stroke-width="5" stroke-linecap="round">
      <circle cx="38" cy="32" r="20"/>
      <path d="M12 10 A30 30 0 0 0 12 54 M64 10 A30 30 0 0 1 64 54"/>
      <line x1="38" y1="21" x2="38" y2="35"/>
      <circle cx="38" cy="43" r="1.5" fill="var(--yellow)"/>
    </svg>
    <svg width="84" height="64" viewBox="0 0 84 64" fill="var(--yellow)" stroke="var(--yellow)" stroke-width="5" stroke-linecap="round">
      <path d="M40 12 C62 12 74 20 74 32 C74 44 62 52 40 52 Z" stroke="none"/>
      <line x1="6" y1="18" x2="28" y2="18"/>
      <line x1="6" y1="32" x2="28" y2="32"/>
      <line x1="6" y1="46" x2="28" y2="46"/>
    </svg>
    <svg width="100" height="64" viewBox="0 0 100 64" fill="var(--yellow)" stroke="var(--yellow)" stroke-width="5" stroke-linecap="round">
      <path d="M28 24 L70 10 L70 54 L28 40 Z" stroke="none"/>
      <rect x="18" y="24" width="12" height="16" stroke="none"/>
      <path d="M78 18 L92 10 M80 32 L96 32 M78 46 L92 54" fill="none"/>
      <path d="M6 8 L14 14 M4 32 L12 32" fill="none"/>
    </svg>
    <svg width="100" height="64" viewBox="0 0 100 64" fill="none" stroke="var(--yellow)" stroke-width="5" stroke-linejoin="round">
      <path d="M4 32 L28 10 L28 24 L44 24 L44 40 L28 40 L28 54 Z"/>
      <path d="M96 32 L72 10 L72 24 L56 24 L56 40 L72 40 L72 54 Z"/>
    </svg>
  </div>
</main>
</body>
</html>
```